Meadowlark Property Review is a leading provider of residential appraisal and home inspection products in S

I need a business card/logo designed that obviously describes my business. We are a residential appraisal and home inspection company in Springfield, MO. We offer residential appraisals, home inspection, pest inspection and radon gas measurement. We have been in business for 18 years and hold state certified residential appraisal licenses and OBREX certified home inspection licenses. I have a logo that I really like and will attach, but would be open to new suggestions. I like more modern designs than traditional and would like a two sided card with our services, licenses and qualifications on the back.

```html
<!DOCTYPE html>
<html lang="en">
<head>
<meta charset="utf-8">
<title>Meadowlark Property Review – Business Card</title>
<link rel="stylesheet" href="https://fonts.googleapis.com/css2?family=PT+Sans:ital,wght@0,400;0,700;1,400&display=swap">
<style>
  :root {
    --backdrop: #3b3b3b;
    --card-white: #f7f7f7;
    --brand-brown: #8d6a43;
    --brand-brown-deep: #85643f;
    --brand-orange: #f0901e;
    --text-light: #ffffff;
    --text-muted: #555555;
  }
  * { box-sizing: border-box; margin: 0; padding: 0; }
  html, body {
    width: 1200px; height: 750px; overflow: hidden;
    background: var(--backdrop);
    font-family: "PT Sans", sans-serif;
  }
  .stage { position: relative; width: 1200px; height: 750px; }
  .card {
    position: absolute; top: 228px; width: 461px; height: 262px;
    overflow: hidden; background: var(--card-white);
  }
  .card--front { left: 124px; background: var(--brand-brown); }
  .card--back { left: 618px; }
  .roof-bands { position: absolute; inset: 0; width: 100%; height: 100%; }

  .contact { position: absolute; left: 32px; top: 52px; color: var(--text-light); }
  .contact__name { color: var(--brand-orange); font-size: 17px; line-height: 1.1; }
  .contact__role { font-size: 13px; margin-top: 2px; }
  .contact__address { font-size: 11px; line-height: 14px; margin-top: 18px; }
  .contact__list { list-style: none; margin-top: 12px; font-size: 11px; }
  .contact__list li { display: flex; align-items: center; height: 17.5px; white-space: nowrap; }
  .contact__icon { width: 12px; height: 12px; margin-right: 6px; fill: var(--brand-orange); flex: none; }

  .brand-name {
    position: absolute; left: 262px; top: 184px; width: 190px;
    text-align: center; color: var(--brand-brown);
    font-size: 17px; font-weight: 700; line-height: 1.15;
  }

  .back-brand {
    position: absolute; left: 0; right: 0; top: 100px;
    text-align: center; color: var(--brand-brown);
    font-size: 24px; font-weight: 700;
  }
  .services {
    position: absolute; left: 0; right: 0; top: 198px;
    text-align: center; color: var(--text-muted);
    font-size: 12px; font-style: italic; line-height: 18px;
  }
  .services__dot { color: var(--brand-orange); font-style: normal; }
</style>
</head>
<body>
<main class="stage">
  <section class="card card--front" aria-label="Card front">
    <svg class="roof-bands" viewBox="0 0 576 328" preserveAspectRatio="none" aria-hidden="true">
      <polyline points="157,328 476,9 576,109" fill="none" stroke="#ffffff" stroke-width="3"/>
      <polygon points="476,20 476,55 200,328 166,328" fill="var(--brand-brown-deep)"/>
      <polygon points="476,20 576,118 576,150 476,55" fill="var(--brand-orange)"/>
      <polygon points="476,55 576,150 576,328 200,328" fill="var(--card-white)"/>
    </svg>

    <div class="contact">
      <p class="contact__name">Dana Whitfield</p>
      <p class="contact__role">CEO/Founder</p>
      <p class="contact__address">412 Larkspur Court<br>Springfield, Missouri 65804</p>
      <ul class="contact__list">
        <li><svg class="contact__icon" viewBox="0 0 24 24"><path d="M6.6 10.8a15 15 0 0 0 6.6 6.6l2.2-2.2c.3-.3.7-.4 1-.2 1.1.4 2.3.6 3.6.6.6 0 1 .4 1 1V20c0 .6-.4 1-1 1A17 17 0 0 1 3 4c0-.6.4-1 1-1h3.5c.6 0 1 .4 1 1 0 1.3.2 2.5.6 3.6.1.3 0 .7-.2 1z"/></svg>417 555 0182</li>
        <li><svg class="contact__icon" viewBox="0 0 24 24"><path d="M6 3h10l2 2v4H6zM3 10h18a1 1 0 0 1 1 1v7h-4v3H6v-3H2v-7a1 1 0 0 1 1-1zm5 6v3h8v-3z"/></svg>417 555 0147</li>
        <li><svg class="contact__icon" viewBox="0 0 24 24"><path d="M2 5h20v14H2zm2 2v.5l8 5 8-5V7z"/></svg>dana@mlreview.com</li>
        <li><svg class="contact__icon" viewBox="0 0 24 24"><path d="M12 2a10 10 0 1 0 0 20 10 10 0 0 0 0-20zm-1 17.9A8 8 0 0 1 4.2 10L9 14.8v1a2 2 0 0 0 2 2zm6.9-2.5A2 2 0 0 0 16 16h-1v-3a1 1 0 0 0-1-1H8v-2h2a1 1 0 0 0 1-1V7h2a2 2 0 0 0 2-2v-.4a8 8 0 0 1 2.9 12.8z"/></svg>www.mlreview.com</li>
      </ul>
    </div>

    <p class="brand-name">Meadowlark<br>Property Review</p>
  </section>

  <section class="card card--back" aria-label="Card back">
    <p class="back-brand">Meadowlark Property Review</p>
    <p class="services">
      Residential appraisals <span class="services__dot">•</span> Home inspection<br>
      Pest inspection and radon gas measurement.
    </p>
  </section>
</main>
</body>
</html>
```